Rollway Stays

We are 100% online, promoting accommodation details and booking facilities for wheelchair dependant travellers.
Listings will only be accommodation providers which meet our specific criteria.

Target Market(s)

Wheelchair dependant people and their companions

Industry/Entity Type

Accommodation

Contact Information for Business Card

Name, mobile phone number, email address, website address

```html
<!DOCTYPE html>
<html lang="en">
<head>
<meta charset="utf-8">
<title>Rollway Stays – Business Card</title>
<link href="https://fonts.googleapis.com/css2?family=Jura:wght@400;500;600;700&display=swap" rel="stylesheet">
<style>
  :root {
    --backdrop: #e9e6e1;
    --card-white: #ffffff;
    --brand-blue: #29a9e1;
    --panel-blue: #31b0e8;
    --slate: #7b7d80;
    --slate-dark: #5f6164;
    --rule: #c98a7a;
    --ink-light: #ffffff;
  }
  * { box-sizing: border-box; margin: 0; padding: 0; }
  html, body {
    width: 1200px; height: 672px; overflow: hidden;
    background: var(--backdrop);
    font-family: "Jura", sans-serif;
  }
  .canvas {
    position: relative; width: 1200px; height: 672px;
    display: flex; align-items: center; justify-content: center;
  }
  .business-card {
    position: relative; width: 340px; height: 596px;
    background: var(--card-white);
    box-shadow: 0 6px 24px rgba(0,0,0,0.18);
    overflow: hidden;
  }
  .top-tab {
    position: absolute; top: 0; left: 16px; right: 16px; height: 22px;
    background: var(--slate);
    border-radius: 0 0 10px 10px;
  }
  .brand {
    position: absolute; top: 62px; left: 0; right: 0; text-align: center;
  }
  .brand-name {
    color: var(--brand-blue); font-weight: 700; font-size: 34px;
    letter-spacing: 2px; text-transform: uppercase; line-height: 1;
  }
  .brand-descriptor {
    margin-top: 6px; color: var(--slate-dark); font-weight: 600;
    font-size: 14px; letter-spacing: 1.6px; text-transform: uppercase;
  }
  .contact-panel {
    position: absolute; top: 168px; left: 16px; right: 16px; height: 300px;
    background: var(--panel-blue);
    border-radius: 14px;
    color: var(--ink-light);
  }
  .person { text-align: center; padding-top: 22px; }
  .person-name { font-size: 21px; font-weight: 600; letter-spacing: 1.5px; text-transform: uppercase; }
  .person-role { font-size: 14px; font-weight: 600; letter-spacing: 1.2px; text-transform: uppercase; margin-top: 2px; }
  .panel-rule { height: 1.5px; background: var(--rule); margin: 14px 0 0; }
  .contact-list { list-style: none; padding: 18px 0 0 34px; }
  .contact-item {
    display: flex; align-items: center; gap: 12px;
    font-size: 15px; font-weight: 500; letter-spacing: 0.8px; height: 34px;
  }
  .contact-icon { width: 20px; height: 20px; flex: none; }
  .address-band {
    position: absolute; left: 16px; right: 16px; bottom: 0; height: 150px;
    background: var(--slate);
    border-radius: 14px 14px 0 0;
    color: var(--ink-light);
  }
  .address { display: flex; gap: 12px; padding: 48px 0 0 34px; font-size: 15px; font-weight: 500; letter-spacing: 0.8px; line-height: 1.45; }
  .address .contact-icon { margin-top: 2px; }
</style>
</head>
<body>
<main class="canvas">
  <article class="business-card">
    <div class="top-tab"></div>

    <header class="brand">
      <div class="brand-name">Rollway Stays</div>
      <div class="brand-descriptor">Accessible Accommodation</div>
    </header>

    <section class="contact-panel">
      <div class="person">
        <div class="person-name">Dana Reyes</div>
        <div class="person-role">General Manager</div>
      </div>
      <div class="panel-rule"></div>
      <ul class="contact-list">
        <li class="contact-item">
          <svg class="contact-icon" viewBox="0 0 20 20" fill="none" stroke="currentColor" stroke-width="1.4"><circle cx="10" cy="10" r="9"/><path d="M7 5.5l1.6 2-1 1.2c.7 1.5 1.7 2.5 3.2 3.2l1.2-1 2 1.6-1 1.6c-3.6-.4-6.3-3.1-6.7-6.7z" fill="currentColor" stroke="none"/></svg>
          <span>012 555 0142</span>
        </li>
        <li class="contact-item">
          <svg class="contact-icon" viewBox="0 0 20 20" fill="none" stroke="currentColor" stroke-width="1.4"><circle cx="10" cy="10" r="9"/><rect x="7" y="5" width="6" height="10" rx="1"/><line x1="9.2" y1="13" x2="10.8" y2="13"/></svg>
          <span>012 555 0143</span>
        </li>
        <li class="contact-item">
          <svg class="contact-icon" viewBox="0 0 20 20" fill="none" stroke="currentColor" stroke-width="1.4"><circle cx="10" cy="10" r="9"/><rect x="6" y="8" width="8" height="6" rx="1"/><path d="M7.5 8V5.5h5V8"/></svg>
          <span>012 555 0144</span>
        </li>
        <li class="contact-item">
          <svg class="contact-icon" viewBox="0 0 20 20" fill="none" stroke="currentColor" stroke-width="1.4"><circle cx="10" cy="10" r="9"/><rect x="5.5" y="6.5" width="9" height="7" rx="0.8"/><path d="M5.5 7l4.5 3.5L14.5 7"/></svg>
          <span>dana@rollway.example</span>
        </li>
        <li class="contact-item">
          <svg class="contact-icon" viewBox="0 0 20 20" fill="none" stroke="currentColor" stroke-width="1.4"><circle cx="10" cy="10" r="9"/><circle cx="10" cy="10" r="5"/><path d="M5 10h10M10 5c-2 2.8-2 7.2 0 10M10 5c2 2.8 2 7.2 0 10"/></svg>
          <span>www.rollwaystays.example</span>
        </li>
      </ul>
    </section>

    <footer class="address-band">
      <div class="address">
        <svg class="contact-icon" viewBox="0 0 20 20" fill="none" stroke="currentColor" stroke-width="1.4"><circle cx="10" cy="10" r="9"/><path d="M10 15s-3.5-3.6-3.5-6.2a3.5 3.5 0 017 0C13.5 11.4 10 15 10 15z"/><circle cx="10" cy="8.8" r="1.2"/></svg>
        <span>24 Harbor Lane Road<br>5th building Street</span>
      </div>
    </footer>
  </article>
</main>
</body>
</html>
```